Website redesign www.marigoldlawpc.com law firm site

Need to redesign the website that I currently have to look more modern and professional. Would also like to be able to make updates and post without having a huge hassle. See current www.marigoldlawpc.com. I just think that it looks very immature and it's very templated there's no ability for me to make posts or Add links or anything like that

Target Market(s)

California people looking for a powerhouse attorney in

Industry/Entity Type

Legal

Number of Pages Required

3 page

Font styles to use
Serif
Sans Serif

Colors
ec1f27
000000
ffffff

Requirements
Must have
• Must be mobile friendly. Must look professional and have ability to post links to other websites. Must have ability to post blogs or articles. Would like to be able to read my FeeTrove account and also have the ability to upload forms for people to download
Nice to have
• Simple design easy to use and not cluttered with too much text

```html
<!DOCTYPE html>
<html lang="en">
<head>
<meta charset="utf-8">
<title>Marigold Law P.C.</title>
<link href="https://fonts.googleapis.com/css2?family=Cinzel:wght@400;700&family=Lato:wght@400;700&family=Raleway:wght@700&display=swap" rel="stylesheet">
<style>
:root{
  --red:#ec1f27;
  --black:#000;
  --white:#fff;
  --ink:#222;
  --grey-panel:#5b5b5b;
  --grey-light:#efefef;
  --footer:#2d2d2d;
  --footer-text:#c9c9c9;
}
*{margin:0;padding:0;box-sizing:border-box}
html,body{width:1200px;height:2821px;overflow:hidden}
body{position:relative;background:var(--white);font-family:'Lato',sans-serif;color:var(--ink)}
.abs{position:absolute}

/* header */
.top-rule{left:0;top:0;width:1200px;height:6px;background:var(--black)}
.logo{left:66px;top:18px;font-family:'Cinzel',serif;font-weight:400;color:var(--red);font-size:42px;letter-spacing:1px;line-height:1}
.logo small{display:block;font-size:20px;text-align:center;margin-top:4px}
.contact-top{left:885px;font-size:15px;color:var(--ink);display:flex;align-items:center;gap:12px}
.contact-top .ico{width:26px;height:26px;border-radius:50%;background:var(--black);display:flex;align-items:center;justify-content:center}

/* nav */
.nav{left:0;top:107px;width:1200px;height:43px;background:var(--black);display:flex;padding-left:66px}
.nav a{color:var(--white);text-decoration:none;font-size:15px;font-weight:700;display:flex;align-items:center;justify-content:center;border-right:1px solid #444;height:100%}
.nav a.active{background:var(--red)}
.nav a:last-child{border-right:none}

/* hero */
.hero{left:0;top:150px;width:1200px;height:427px;background:linear-gradient(100deg,#2b1a10 0%,#6a4a2e 30%,#b89a74 55%,#e5d6bd 80%,#f0e6d4 100%)}
.hero-text{right:68px;top:288px;width:500px;text-align:right;font-family:'Raleway',sans-serif;font-weight:700;font-size:25px;line-height:37px;color:#1a1a1a;text-shadow:0 0 6px rgba(255,255,255,.8)}
.chev{top:320px}

/* welcome */
.welcome-h{left:66px;top:645px;font-family:'Cinzel',serif;font-size:33px;color:var(--black)}
.welcome-h span{color:var(--red)}
.rule{height:1px;background:#999}
.welcome-p{left:66px;top:707px;width:680px;font-size:15px;line-height:25px;color:#333}
.welcome-p p{margin-bottom:10px}
.pill-btn{display:flex;align-items:center;height:36px;border-radius:18px;color:var(--white);font-size:11px;font-weight:700;text-transform:uppercase;padding-left:10px}
.pill-btn .arr{width:38px;height:38px;border-radius:50%;background:var(--black);border:2px solid #888;margin-left:auto;display:flex;align-items:center;justify-content:center}

.inquiry{left:803px;top:641px;width:327px;height:335px;background:var(--grey-panel)}
.inquiry h3{font-family:'Cinzel',serif;font-weight:400;color:var(--white);font-size:29px;text-align:center;margin-top:28px;letter-spacing:1px}
.field{position:absolute;left:19px;width:290px;background:var(--white);font-size:12px;color:#555;padding:10px}

/* practice */
.practice{left:0;top:1044px;width:1200px;height:400px;background:var(--black)}
.sec-title{font-family:'Cinzel',serif;color:var(--white);font-size:34px;text-align:center;width:1200px;left:0}
.area{width:200px;text-align:center;color:var(--white);font-size:18px;font-weight:700;line-height:25px}
.area .circ{width:136px;height:136px;border-radius:50%;border:3px solid var(--white);margin:0 auto 16px;display:flex;align-items:center;justify-content:center}
.area .circ.on{background:var(--white)}

/* profile */
.profile{left:0;top:1444px;width:1200px;height:371px;background:linear-gradient(90deg,#f6f6f6,#e6e6e6 60%,#f1f1f1)}
.photo-frame{left:66px;top:1505px;width:248px;height:244px;background:var(--black);padding:10px}
.photo{width:100%;height:100%;border:2px solid var(--white);background:linear-gradient(160deg,#6a4a36,#c69a7e 50%,#3a2a20)}
.prof-label{left:370px;top:1508px;font-size:19px;color:#222}
.prof-name{left:370px;top:1532px;font-family:'Cinzel',serif;font-size:31px;color:var(--red);white-space:nowrap}
.prof-name span{color:var(--black);font-size:21px}
.prof-p{left:370px;top:1596px;width:774px;font-size:12.5px;line-height:20px;color:#222}

/* blog + testimonials */
.dark{left:0;top:1815px;width:1200px;height:498px;background:radial-gradient(ellipse at 50% 40%,#4a3524,#241a12 55%,#120d09)}
.h-light{font-family:'Cinzel',serif;color:var(--white);font-size:30px;letter-spacing:1px}
.dots{display:flex;gap:6px}
.dots i{width:18px;height:18px;border-radius:50%;border:2px solid var(--white);display:block}
.post{left:66px;width:446px;display:flex;gap:12px}
.thumb{width:90px;height:56px;flex:none;background:linear-gradient(135deg,#d8d2c6,#8a7f70);border:2px solid #ddd}
.post h4{color:var(--white);font-size:13px;font-weight:700;margin-bottom:4px}
.post p{color:#ddd;font-size:13px;line-height:19px}
.post a{color:var(--red);font-size:11px}
.avatar{width:112px;height:112px;border-radius:50%;border:4px solid var(--white);background:linear-gradient(160deg,#8a6a52,#d2b49a)}
.quote{left:822px;width:312px;color:#e6e6e6;font-size:12.5px;line-height:20px}
.quote .who{color:var(--red);font-family:'Cinzel',serif;font-size:12px;margin-top:8px;padding-bottom:6px;border-bottom:1px solid #666}

/* ratings */
.ratings-h{left:147px;top:2390px;font-family:'Cinzel',serif;font-size:29px;color:#222;letter-spacing:1px}

/* footer */
.footer{left:0;top:2505px;width:1200px;height:269px;background:var(--footer)}
.f-title{font-family:'Cinzel',serif;color:#ddd;font-size:17px;letter-spacing:1px;padding-bottom:8px;border-bottom:1px solid #555}
.f-links{list-style:none;font-size:12px;color:var(--footer-text);line-height:21px}
.f-links li:before{content:"› ";}
.f-text{font-size:12px;color:var(--footer-text);line-height:20px}
.bottom{left:0;top:2774px;width:1200px;height:47px;background:var(--black);color:var(--white);font-size:11px}
.soc{width:30px;height:30px;border-radius:50%;border:2px solid var(--white);background:#1f5da8}
.card{width:32px;height:18px;background:#ddd;border-radius:2px}
</style>
</head>
<body>

<div class="abs top-rule"></div>
<div class="abs logo">Marigold Law<small>P.C.</small></div>

<div class="abs contact-top" style="top:21px">
  <span class="ico"><svg width="14" height="14" viewBox="0 0 24 24"><path fill="#fff" d="M6.6 10.8a15 15 0 0 0 6.6 6.6l2.2-2.2c.3-.3.7-.4 1-.2 1.1.4 2.3.6 3.6.6.6 0 1 .4 1 1V20c0 .6-.4 1-1 1A17 17 0 0 1 3 4c0-.6.4-1 1-1h3.5c.6 0 1 .4 1 1 0 1.3.2 2.5.6 3.6.1.3 0 .7-.2 1z"/></svg></span>
  (530) 555-0142
</div>
<div class="abs contact-top" style="top:62px">
  <span class="ico"><svg width="14" height="14" viewBox="0 0 24 24"><path fill="#fff" d="M3 6h18v12H3z"/><path d="M3 6l9 7 9-7" stroke="#000" stroke-width="2" fill="none"/></svg></span>
  renata@marigoldlawgroup.com
</div>

<nav class="abs nav">
  <a class="active" style="width:141px">Home</a>
  <a style="width:207px">Attorney Profile</a>
  <a style="width:207px">Practice Area&nbsp;▾</a>
  <a style="width:207px">Client Reviews</a>
  <a style="width:133px">Links</a>
  <a style="width:172px">Contact us</a>
</nav>

<div class="abs hero" role="img" aria-label="Wooden judge's gavel resting on its block in warm light"></div>
<div class="abs hero-text">A Boutique Law Firm Opportunity For Clients Who Want To Enjoy All The Advantages Of Renata's Broad Legal Experience And Education.</div>
<svg class="abs chev" style="left:24px" width="24" height="96" viewBox="0 0 24 96"><path d="M22 2 2 48l20 46" stroke="#fff" stroke-width="2" fill="none"/></svg>
<svg class="abs chev" style="left:1152px" width="24" height="96" viewBox="0 0 24 96"><path d="M2 2l20 46L2 94" stroke="#fff" stroke-width="2" fill="none"/></svg>

<h2 class="abs welcome-h">Welcome to <span>Marigold Law P.C</span></h2>
<div class="abs rule" style="left:66px;top:696px;width:680px"></div>
<div class="abs welcome-p">
  <p>At Marigold Law, P.C., we offer the following clients services to help you manage all areas of your life that may ever need legal attention</p>
  <p>Marigold Law P.C. is owned by Renata L. Marigold, a dedicated and caring professional who uses her broad range of skills as a California lawyer to bring consumers and business owners exceptionally strong legal representation that achieves best results. She works with people from across the northern region of California, from the Northern border to the Central Valley region. They bring her legal concerns and problems that occur in many areas of law, including Real Estate, Family law, Business Law, Bankruptcy, Criminal Law and Civil Litigation</p>
</div>
<div class="abs pill-btn" style="left:66px;top:936px;width:126px;background:#555">Read more
  <span class="arr"><svg width="10" height="12" viewBox="0 0 10 12"><path d="M2 1l5 5-5 5" stroke="#fff" stroke-width="2" fill="none"/></svg></span></div>

<section class="abs inquiry">
  <h3>Quick Inquiry</h3>
  <div class="field" style="top:89px;height:37px">Name</div>
  <div class="field" style="top:138px;height:37px">Email</div>
  <div class="field" style="top:187px;height:75px">Message</div>
  <div class="pill-btn" style="position:absolute;left:19px;top:275px;width:124px;background:#8a8a8a;height:34px">Submit
    <span class="arr" style="width:40px;height:40px"><svg width="10" height="12" viewBox="0 0 10 12"><path d="M2 1l5 5-5 5" stroke="#fff" stroke-width="2" fill="none"/></svg></span></div>
</section>

<section class="abs practice">
  <h2 class="abs sec-title" style="top:56px;font-weight:400">Our Practice Areas</h2>
  <div class="abs" style="left:310px;top:116px;width:580px;height:1px;background:#888"></div>
  <div class="abs" style="left:596px;top:112px;width:8px;height:8px;border-radius:50%;background:var(--white)"></div>
  <svg class="abs" style="left:22px;top:214px" width="24" height="64" viewBox="0 0 24 64"><path d="M22 2 2 32l20 30" stroke="#fff" stroke-width="2" fill="none"/></svg>
  <svg class="abs" style="left:1154px;top:214px" width="24" height="64" viewBox="0 0 24 64"><path d="M2 2l20 30L2 62" stroke="#fff" stroke-width="2" fill="none"/></svg>

  <div class="abs area" style="left:99px;top:148px"><div class="circ on">
    <svg width="64" height="52" viewBox="0 0 64 52"><rect x="2" y="12" width="60" height="38" rx="3" fill="none" stroke="#000" stroke-width="4"/><path d="M22 12V4h20v8M2 26h60" stroke="#000" stroke-width="4" fill="none"/><rect x="28" y="22" width="8" height="8" fill="#000"/></svg>
  </div>Business<br>Law</div>
  <div class="abs area" style="left:299px;top:148px"><div class="circ">
    <svg width="64" height="60" viewBox="0 0 64 60"><path d="M4 30 32 6l28 24" stroke="#fff" stroke-width="5" fill="none"/><path d="M12 26v30h40V26" stroke="#fff" stroke-width="4" fill="none"/><rect x="24" y="36" width="16" height="20" fill="#fff"/></svg>
  </div>Real Estate<br>Law</div>
  <div class="abs area" style="left:500px;top:148px"><div class="circ">
    <svg width="64" height="64" viewBox="0 0 64 64"><circle cx="32" cy="32" r="27" fill="none" stroke="#fff" stroke-width="4"/><text x="32" y="44" text-anchor="middle" fill="#fff" font-family="Lato,sans-serif" font-weight="700" font-size="34">$</text></svg>
  </div>Bankruptcy</div>
  <div class="abs area" style="left:700px;top:148px"><div class="circ">
    <svg width="64" height="60" viewBox="0 0 64 60"><path d="M4 28 32 4l28 24" stroke="#fff" stroke-width="4" fill="none"/><circle cx="22" cy="28" r="5" fill="#fff"/><circle cx="42" cy="28" r="5" fill="#fff"/><circle cx="32" cy="38" r="4" fill="#fff"/><rect x="16" y="35" width="12" height="22" rx="3" fill="#fff"/><rect x="36" y="35" width="12" height="22" rx="3" fill="#fff"/><rect x="28" y="44" width="8" height="13" rx="2" fill="#fff"/></svg>
  </div>Family<br>Law</div>
  <div class="abs area" style="left:899px;top:148px"><div class="circ">
    <svg width="64" height="48" viewBox="0 0 64 48"><circle cx="18" cy="28" r="13" fill="none" stroke="#fff" stroke-width="5"/><circle cx="46" cy="28" r="13" fill="none" stroke="#fff" stroke-width="5"/><path d="M26 14h12" stroke="#fff" stroke-width="4"/></svg>
  </div>Criminal<br>Law</div>
</section>

<section class="abs profile" role="img" aria-label="Faint courtroom backdrop"></section>
<div class="abs photo-frame"><div class="photo" role="img" aria-label="Portrait photo of attorney Renata L. Marigold"></div></div>
<div class="abs prof-label">Attorney Profile</div>
<div class="abs prof-name">Renata L. Marigold, Esq. <span>Attorney at Marigold Law P.C</span></div>
<div class="abs rule" style="left:370px;top:1584px;width:770px;background:#777"></div>
<div class="abs" style="left:1138px;top:1581px;width:7px;height:7px;border-radius:50%;background:#222"></div>
<p class="abs prof-p">Renata L. Marigold, Esq., is an Attorney who created a small boutique firm where she has the flexibility to build long-term, lasting relationships with clients. Renata provides all of her clients' legal needs through consultation, direct representation and/or qualified referrals. She recognizes the importance of client referrals, and works hard for her clients in every situation. Client referrals are the best way to grow a business, and Renata intends to have a superb reputation for being an excellent attorney and friend to her client base.</p>
<div class="abs pill-btn" style="left:370px;top:1709px;width:180px;background:var(--red);border-radius:3px 18px 18px 3px;text-transform:none;font-weight:400;font-size:12px;line-height:13px">Call Us for<br>Free Consultation
  <span class="arr"><svg width="10" height="12" viewBox="0 0 10 12"><path d="M2 1l5 5-5 5" stroke="#fff" stroke-width="2" fill="none"/></svg></span></div>

<section class="abs dark" role="img" aria-label="Dim backdrop of a gavel and law books"></section>
<h2 class="abs h-light" style="left:66px;top:1870px;font-weight:400">Blog Posts</h2>
<div class="abs dots" style="left:470px;top:1880px"><i></i><i></i></div>
<div class="abs rule" style="left:66px;top:1918px;width:446px;background:#777"></div>

<div class="abs post" style="top:1950px"><div class="thumb" role="img" aria-label="Blog thumbnail photo"></div><div><h4>Duis autem vel eum iriure dolor in hendrerit molestie</h4><p>Lorem ipsum dolor sit amet, consectetuer adipi diam nonummy nibh euismod tincidunt ut laoreet</p><a>Read More »</a></div></div>
<div class="abs post" style="top:2063px"><div class="thumb" role="img" aria-label="Blog thumbnail photo"></div><div><h4>Duis autem vel eum iriure dolor in hendrerit molestie</h4><p>Lorem ipsum dolor sit amet, consectetuer adipi diam nonummy nibh euismod tincidunt ut laoreet</p><a>Read More »</a></div></div>
<div class="abs post" style="top:2176px"><div class="thumb" role="img" aria-label="Blog thumbnail photo"></div><div><h4>Duis autem vel eum iriure dolor in hendrerit molestie</h4><p>Lorem ipsum dolor sit amet, consectetuer adipi diam nonummy nibh euismod tincidunt ut laoreet</p><a>Read More »</a></div></div>

<h2 class="abs h-light" style="left:686px;top:1870px;font-weight:400">Client Testimonials</h2>
<div class="abs dots" style="left:1090px;top:1880px"><i></i><i></i></div>
<div class="abs rule" style="left:686px;top:1918px;width:448px;background:#777"></div>

<div class="abs avatar" style="left:687px;top:1953px" role="img" aria-label="Client portrait photo"></div>
<div class="abs quote" style="top:1950px">“ Marigold Law is our go-to source for professional and sound legal advice. Marigold Law has become a vital component to the success of our business as well as the businesses of the clients we have referred to Marigold Law. ”<div class="who">Cedar Ridge Accounting Partners</div></div>
<div class="abs avatar" style="left:687px;top:2116px" role="img" aria-label="Client portrait photo"></div>
<div class="abs quote" style="top:2116px">“ Marigold Law has met and exceeded our expectations in assisting our company with our real estate legal needs. In an area of law where the rules our ever changing, we simply could not navigate our company effectively without their help. ”<div class="who">Halden Commercial</div></div>

<h2 class="abs ratings-h" style="font-weight:400">Ratings and Reviews:</h2>
<div class="abs" style="left:536px;top:2350px;width:120px;height:120px;border-radius:50%;background:#1f4f8c" role="img" aria-label="Attorney rating badge"></div>
<div class="abs" style="left:680px;top:2352px;width:114px;height:114px;border-radius:50%;border:4px solid #555" role="img" aria-label="State bar seal"></div>
<div class="abs" style="left:820px;top:2384px;width:237px;height:52px;background:#3e5f8e" role="img" aria-label="Lawyer directory listing badge"></div>

<footer class="abs footer">
  <div class="abs" style="left:66px;top:45px;width:185px"><div class="f-title">Quick Links</div>
    <ul class="f-links" style="margin-top:10px"><li>Home</li><li>Attorney Profile</li><li>Practice Area</li><li>Client Reviews</li><li>Links</li><li>Contact us</li></ul></div>
  <div class="abs" style="left:293px;top:45px;width:248px"><div class="f-title">Newsletter Sign Up</div>
    <p class="f-text" style="margin-top:12px">Get latest update by entering your email address.</p>
    <div style="margin-top:16px;height:34px;border:1px solid #aaa;color:#ddd;font-size:12px;padding:9px 10px">Email Address</div>
    <div style="margin-top:16px;width:96px;height:30px;background:#fff;color:#222;font-size:11px;font-weight:700;display:flex;align-items:center;justify-content:center">SUBSCRIBE</div></div>
  <div class="abs" style="left:589px;top:45px;width:1px;height:190px;background:#555"></div>
  <div class="abs" style="left:643px;top:45px;width:491px"><div class="f-title">Contact Details</div></div>
  <div class="abs" style="left:645px;top:85px;width:261px;height:103px;background:linear-gradient(135deg,#e8e4da,#cfd8c8)" role="img" aria-label="Street map of the office location"></div>
  <div class="abs f-text" style="left:935px;top:80px;line-height:21px">
    <div style="display:flex;gap:12px"><svg width="12" height="16" viewBox="0 0 12 16"><path d="M6 0a6 6 0 0 0-6 6c0 4 6 10 6 10s6-6 6-10a6 6 0 0 0-6-6z" fill="#ddd"/><circle cx="6" cy="6" r="2" fill="#2d2d2d"/></svg><div><b style="color:#eee">Marigold Law, P.C. Office</b><br>48 Orchard Lane, Suite 310<br>Redding, CA 96001</div></div>
    <div style="display:flex;gap:12px;margin-top:6px"><svg width="12" height="14" viewBox="0 0 24 24"><path fill="#ddd" d="M6.6 10.8a15 15 0 0 0 6.6 6.6l2.2-2.2c.3-.3.7-.4 1-.2 1.1.4 2.3.6 3.6.6.6 0 1 .4 1 1V20c0 .6-.4 1-1 1A17 17 0 0 1 3 4c0-.6.4-1 1-1h3.5c.6 0 1 .4 1 1 0 1.3.2 2.5.6 3.6.1.3 0 .7-.2 1z"/></svg>(530) 555-0142</div>
    <div style="display:flex;gap:12px;margin-top:6px"><svg width="12" height="14" viewBox="0 0 12 14"><rect x="0" y="4" width="12" height="8" fill="#ddd"/><rect x="3" y="0" width="6" height="4" fill="#ddd"/></svg>(888) 555-0187</div>
    <div style="display:flex;gap:12px;margin-top:6px;align-items:center"><svg width="12" height="10" viewBox="0 0 12 10"><rect width="12" height="10" fill="#ddd"/><path d="M0 0l6 5 6-5" stroke="#2d2d2d" fill="none"/></svg>renata@marigoldlawgroup.com</div>
  </div>
</footer>

<div class="abs bottom">
  <div class="abs" style="left:66px;top:17px">Copyright © 2016 <b>Marigold Law P.C.</b> All Rights Reserved.</div>
  <div class="abs" style="left:481px;top:17px;font-weight:700">Follow Us:</div>
  <div class="abs soc" style="left:559px;top:8px"></div>
  <div class="abs soc" style="left:602px;top:8px;background:#2a77b5"></div>
  <div class="abs soc" style="left:643px;top:8px;background:#3d8fd6"></div>
  <div class="abs" style="left:777px;top:17px;font-weight:700">Pay Your Invoice:</div>
  <div class="abs" style="left:890px;top:14px;font-size:15px;font-weight:700">FeeTrove</div>
  <div class="abs" style="left:993px;top:14px;display:flex;gap:5px"><i class="card"></i><i class="card"></i><i class="card"></i><i class="card"></i></div>
</div>

</body>
</html>
```